Redesign two existing website pages and one new landing page for dental office

I need to redesign two webpages on my dental website, the Home page (http://velbridgedental.com) and the Dental Implant Services page (http://www.velbridgedental.com/dental-implant-services) and also create a landing page for the Dental Implant Services page.

Please use the same color scheme, slogans and subtitles for the redesign pages and create a reserved video spot on each page. The video spots should not be too big but not too small either and positioned in a central key location on each of the pages. The final redesigned pages should communicate leadership, confidence and trust.

The new landing page for the Dental implant Services page must not have any hyperlinks on the page and must entice the viewer to give name and email before downloading a "Free" eBook called "Is a Fuller Smile Worth the Wait?" Any added photo images to this new page must be smiling.
Updates

Project Deadline Extended Reason: I got feedback that my project was not long enough so I'm extending it by 5 days. Added Thursday, April 16, 2015

Target Market(s)

People who are middle-age to seniors.

Industry/Entity Type

Dental

Coding

Coded - Design and coding required

Number of Pages Required

3 page

Requirements
Must have
• Compatible with existing website colors and theme.

```html
<!DOCTYPE html>
<html lang="en">
<head>
<meta charset="utf-8">
<title>Velbridge Dental Care</title>
<link href="https://fonts.googleapis.com/css2?family=Open+Sans:wght@300;400;600;700;800&display=swap" rel="stylesheet">
<style>
:root{
  --teal:#4d9f92;
  --teal-dark:#2d7d74;
  --band:#8cbcad;
  --ink:#2f3636;
  --text:#5a6262;
  --muted:#8a9292;
  --light:#f1f3f3;
  --nav:#3c4343;
  --footer:#353a3b;
  --footer-deep:#262a2b;
  --white:#ffffff;
}
*{box-sizing:border-box;margin:0;padding:0}
html,body{width:1200px;height:2292px;overflow:hidden;background:var(--white);font-family:'Open Sans',sans-serif;color:var(--text)}
.wrap{width:940px;margin:0 auto;position:relative}
/* header */
.site-header{height:116px}
.site-header .wrap{height:116px;display:flex;align-items:center;justify-content:space-between}
.brand{display:flex;align-items:center;gap:12px;font-size:34px;font-weight:600;color:var(--ink)}
.brand-mark{width:22px;height:22px;border-radius:50%;background:var(--teal)}
.header-phone{text-align:right}
.header-phone .num{font-size:24px;font-weight:700;color:var(--ink);display:flex;align-items:center;gap:8px;justify-content:flex-end}
.header-phone .sub{font-size:12px;color:var(--muted)}
/* nav */
.main-nav{background:var(--nav)}
.main-nav .wrap{height:36px;display:flex;align-items:center;justify-content:space-between}
.nav-links{display:flex;height:36px}
.nav-links a{color:#dfe3e3;font-size:12px;font-weight:600;text-decoration:none;padding:0 20px;display:flex;align-items:center;text-transform:uppercase}
.nav-links a.active{background:var(--teal);color:var(--white)}
.social{display:flex;gap:6px}
.social span{width:20px;height:20px;border-radius:3px;background:#7a8383}
.social span:nth-child(2){background:var(--teal)}
/* hero */
.hero{height:412px;background:linear-gradient(90deg,#e9eff1 0%,#d7e6ea 45%,#cfe2e6 100%);position:relative;overflow:hidden}
.hero-photo{position:absolute;right:0;top:0;width:640px;height:412px;background:radial-gradient(ellipse at 55% 45%,#f3e3d6 0%,#e2cdbd 35%,#c9d9de 75%)}
.hero-copy{position:absolute;left:146px;top:140px}
.hero-copy h1{font-size:34px;line-height:44px;font-weight:800;color:var(--ink);width:430px}
.btn-appt{margin-top:22px;display:inline-flex;align-items:center;gap:10px;background:var(--teal-dark);color:var(--white);font-size:15px;font-weight:600;padding:12px 22px;border-radius:3px}
/* quick links */
.quick{background:var(--light);padding:28px 0}
.quick .wrap{display:flex;justify-content:space-between;padding:0 20px}
.quick-item{display:flex;align-items:center;gap:14px;width:260px}
.quick-icon{width:46px;height:46px;background:var(--ink);border-radius:4px;display:flex;align-items:center;justify-content:center}
.quick-item strong{display:block;font-size:17px;font-weight:600;color:var(--ink);line-height:22px}
/* service columns */
.care{padding:36px 0 50px}
.care .wrap{display:flex;justify-content:space-between}
.care-col{width:440px}
.care-col h2{font-size:22px;font-weight:300;color:var(--ink);text-transform:uppercase;border-bottom:1px solid #dde1e1;padding-bottom:14px;margin-bottom:20px}
.care-body{display:flex;gap:20px}
.care-photo{width:150px;height:150px;border-radius:50%;flex:none}
.care-photo.hygiene{background:radial-gradient(circle,#f4f6f7,#d8e1e4)}
.care-photo.emergency{background:radial-gradient(circle,#f1dcc9,#d9c1ae)}
.care-body h3{font-size:18px;font-weight:600;color:var(--ink);line-height:23px;margin-bottom:8px}
.care-body p{font-size:11.5px;line-height:17px}
.btn-more{display:inline-block;margin-top:12px;background:var(--ink);color:var(--white);font-size:10px;font-weight:700;padding:6px 12px;border-radius:2px}
/* services band */
.services{background:var(--band);padding:50px 0 60px;text-align:center}
.services h2{font-size:34px;font-weight:800;color:var(--ink)}
.services .lead{font-size:15px;font-weight:600;color:var(--ink);margin-top:10px}
.services .rule{width:880px;height:1px;background:#a9cfc3;margin:28px auto 36px}
.service-grid{display:flex;justify-content:space-between}
.service{width:210px}
.service-icon{width:100px;height:100px;border-radius:50%;background:var(--ink);margin:0 auto;display:flex;align-items:center;justify-content:center}
.service h3{font-size:15px;font-weight:800;color:var(--ink);margin:20px 0 10px;text-transform:uppercase}
.service p{font-size:12px;line-height:18px;color:#3c4545}
/* intro + video */
.intro{padding:50px 0 40px}
.intro .wrap{display:flex;justify-content:space-between;align-items:flex-start}
.intro-copy{width:470px}
.intro-copy h2{font-size:26px;line-height:34px;font-weight:700;color:var(--ink);margin-bottom:16px}
.intro-copy p{font-size:12px;line-height:18px}
.video-spot{width:400px;height:230px;background:linear-gradient(135deg,#eef3f5,#d6e3e8 60%,#e8d4c5);position:relative;display:flex;align-items:center;justify-content:center}
/* footer */
.site-footer{background:var(--footer);color:#aab1b1;position:absolute;top:1984px;left:0;width:1200px;height:256px;padding-top:30px}
.site-footer .wrap{display:flex;justify-content:space-between}
.foot-col{width:200px}
.foot-col h4{font-size:12px;font-weight:700;color:var(--white);text-transform:uppercase;margin-bottom:14px}
.foot-col p,.foot-col li{font-size:10.5px;line-height:16px;list-style:none}
.foot-col li{border-bottom:1px solid #464c4d;padding:4px 0}
.foot-col li.boxed{background:#41474a;border:none;margin-bottom:6px;padding:5px 8px}
.legal{position:absolute;top:2240px;left:0;width:1200px;height:52px;background:var(--footer-deep)}
.legal .wrap{height:52px;display:flex;align-items:center;justify-content:space-between;font-size:10px;color:#8a9191}
.legal .social span{background:#4b5253}
</style>
</head>
<body>
<header class="site-header">
  <div class="wrap">
    <div class="brand"><span class="brand-mark"></span>Velbridge Dental Care</div>
    <div class="header-phone">
      <div class="num">
        <svg width="18" height="18" viewBox="0 0 24 24"><path fill="#2f3636" d="M6.6 10.8a15 15 0 006.6 6.6l2.2-2.2a1 1 0 011-.25 11.4 11.4 0 003.6.57 1 1 0 011 1V20a1 1 0 01-1 1A17 17 0 013 4a1 1 0 011-1h3.5a1 1 0 011 1c0 1.25.2 2.45.57 3.57a1 1 0 01-.25 1z"/></svg>
        (555) 240-1187
      </div>
      <div class="sub">Your Smile Is Our Priority</div>
    </div>
  </div>
</header>

<nav class="main-nav">
  <div class="wrap">
    <div class="nav-links">
      <a class="active">Home</a><a>About Us</a><a>Dental Services</a><a>Blog</a><a>Testimonials</a><a>Contact Us</a>
    </div>
    <div class="social"><span></span><span></span><span></span><span></span></div>
  </div>
</nav>

<section class="hero">
  <div class="hero-photo" role="img" aria-label="Photo of a smiling family of three hugging"></div>
  <div class="hero-copy">
    <h1>Life-Changing Family Dental Care In Willow Bend</h1>
    <div class="btn-appt">
      <svg width="16" height="16" viewBox="0 0 16 16"><rect x="1" y="3" width="14" height="12" rx="1" fill="none" stroke="#fff" stroke-width="1.5"/><path d="M1 7h14M5 1v4M11 1v4" stroke="#fff" stroke-width="1.5"/></svg>
      Request an Appointment
    </div>
  </div>
</section>

<section class="quick">
  <div class="wrap">
    <div class="quick-item">
      <div class="quick-icon"><svg width="20" height="28" viewBox="0 0 20 28"><rect x="2" y="1" width="16" height="26" rx="3" fill="none" stroke="#fff" stroke-width="2"/><circle cx="10" cy="22" r="1.6" fill="#fff"/></svg></div>
      <strong>Get Dr. Velbridge's<br>Mobile App</strong>
    </div>
    <div class="quick-item">
      <div class="quick-icon"><svg width="22" height="26" viewBox="0 0 22 26"><rect x="2" y="1" width="18" height="24" rx="2" fill="none" stroke="#fff" stroke-width="2"/><path d="M6 8h10M6 13h10M6 18h6" stroke="#fff" stroke-width="2"/></svg></div>
      <strong>New Patient<br>Online Forms</strong>
    </div>
    <div class="quick-item">
      <div class="quick-icon"><svg width="24" height="24" viewBox="0 0 24 24"><path fill="#fff" d="M6.6 10.8a15 15 0 006.6 6.6l2.2-2.2a1 1 0 011-.25 11.4 11.4 0 003.6.57 1 1 0 011 1V20a1 1 0 01-1 1A17 17 0 013 4a1 1 0 011-1h3.5a1 1 0 011 1c0 1.25.2 2.45.57 3.57a1 1 0 01-.25 1z"/></svg></div>
      <strong>Call Us Today<br>(555) 240-1187</strong>
    </div>
  </div>
</section>

<section class="care">
  <div class="wrap">
    <div class="care-col">
      <h2>Dental Hygiene Services</h2>
      <div class="care-body">
        <div class="care-photo hygiene" role="img" aria-label="Photo of a toothbrush and dental care tools"></div>
        <div>
          <h3>Achieve Better Health With Prevention</h3>
          <p>Regular cleanings and gentle checkups keep teeth strong and gums healthy, so small concerns are caught early by our caring hygiene team.</p>
          <span class="btn-more">READ MORE</span>
        </div>
      </div>
    </div>
    <div class="care-col">
      <h2>Dental Emergency Services</h2>
      <div class="care-body">
        <div class="care-photo emergency" role="img" aria-label="Photo of a patient holding her cheek in tooth pain"></div>
        <div>
          <h3>Stop Pain From Tooth Trauma and Infection</h3>
          <p>Dental emergencies can start with sudden swelling or a broken tooth. Call us right away and we will see you quickly and relieve the pain.</p>
          <span class="btn-more">READ MORE</span>
        </div>
      </div>
    </div>
  </div>
</section>

<section class="services">
  <div class="wrap">
    <h2>OUR SERVICES</h2>
    <p class="lead">Gentle, modern care for every smile, from routine visits to complete restorations.</p>
    <div class="rule"></div>
    <div class="service-grid">
      <div class="service">
        <div class="service-icon"><svg width="46" height="50" viewBox="0 0 46 50"><path d="M12 4c-7 0-10 6-9 13 1 8 4 12 5 20 1 7 3 11 6 11s4-6 5-12c1-4 3-5 4-5s3 1 4 5c1 6 2 12 5 12s5-4 6-11c1-8 4-12 5-20 1-7-2-13-9-13-5 0-7 3-11 3S17 4 12 4z" fill="none" stroke="#fff" stroke-width="3"/></svg></div>
        <h3>Beautiful Dentures</h3>
        <p>Natural looking dentures fitted with care so you can eat, speak and smile with ease every day.</p>
      </div>
      <div class="service">
        <div class="service-icon"><svg width="54" height="30" viewBox="0 0 54 30"><path d="M3 5c8 6 16 8 24 8s16-2 24-8c-3 14-12 22-24 22S6 19 3 5z" fill="none" stroke="#fff" stroke-width="3"/><path d="M12 12l2 8M22 13v9M32 13v9M42 12l-2 8" stroke="#fff" stroke-width="2"/></svg></div>
        <h3>Cosmetic Dentistry</h3>
        <p>Whitening, veneers and bonding that brighten your smile and help you feel confident again.</p>
      </div>
      <div class="service">
        <div class="service-icon"><svg width="36" height="52" viewBox="0 0 36 52"><path d="M4 6c0-3 3-5 7-5 3 0 5 2 7 2s4-2 7-2c4 0 7 2 7 5 0 4-3 9-6 11H10C7 15 4 10 4 6z" fill="none" stroke="#fff" stroke-width="3"/><path d="M10 22h16M11 29h14M12 36h12M14 43h8M16 49h4" stroke="#fff" stroke-width="3"/></svg></div>
        <h3>Dental Implant</h3>
        <p>Permanent implants that replace missing teeth and restore a strong, comfortable bite.</p>
      </div>
      <div class="service">
        <div class="service-icon"><svg width="52" height="40" viewBox="0 0 52 40"><path d="M3 32h46M5 32V20h42v12M3 38v-6M49 38v-6" stroke="#fff" stroke-width="3" fill="none"/><circle cx="13" cy="14" r="5" fill="#fff"/><path d="M30 4h8l-8 8h8" stroke="#fff" stroke-width="2.5" fill="none"/></svg></div>
        <h3>Sedation Dentistry</h3>
        <p>Relaxing sedation options that make every visit calm, comfortable and free of worry.</p>
      </div>
    </div>
  </div>
</section>

<section class="intro">
  <div class="wrap">
    <div class="intro-copy">
      <h2>Comprehensive Family Dentistry in One Willow Bend Dental Office!</h2>
      <p>Our practice offers complete dental care for the whole family under one roof. From first cleanings for children to implants and restorations for adults and seniors, our experienced team takes time to listen, explain each option clearly and deliver lasting results. We use gentle techniques and modern technology to keep every visit comfortable. Patients trust us for honest advice, flexible scheduling and a warm, welcoming office where every smile matters.</p>
    </div>
    <div class="video-spot" role="img" aria-label="Video of the dentist greeting a smiling patient in the office">
      <svg width="64" height="64" viewBox="0 0 64 64"><circle cx="32" cy="32" r="30" fill="rgba(255,255,255,.85)"/><path d="M26 20l18 12-18 12z" fill="#2d7d74"/></svg>
    </div>
  </div>
</section>

<footer class="site-footer">
  <div class="wrap">
    <div class="foot-col">
      <h4>About Us</h4>
      <p>Velbridge Dental Care has served local families for many years with gentle, trusted treatment. Our team focuses on comfort, clear answers and results that last for a lifetime of healthy smiles.</p>
    </div>
    <div class="foot-col">
      <h4>Recent Posts</h4>
      <ul>
        <li class="boxed">Caring For Your New Implants</li>
        <li class="boxed">Simple Tips For Whiter Teeth</li>
        <li class="boxed">When To Replace Dentures</li>
        <li class="boxed">Calm Visits With Sedation</li>
        <li class="boxed">Healthy Gums After Fifty</li>
      </ul>
    </div>
    <div class="foot-col">
      <h4>Navigation</h4>
      <ul>
        <li>Home</li><li>About Us</li><li>Dental Services</li><li>Blog</li><li>Testimonials</li><li>Contact Us</li>
      </ul>
    </div>
    <div class="foot-col">
      <h4>Stay In Touch</h4>
      <p>1200 Harbor Lane, Suite 4<br>Willow Bend, TX 70000<br>(555) 240-1187<br>hello@velbridgedental.com</p>
    </div>
  </div>
</footer>
<div class="legal">
  <div class="wrap">
    <span>© 2015 Velbridge Dental Care. All rights reserved.</span>
    <div class="social"><span></span><span></span><span></span><span></span><span></span></div>
  </div>
</div>
</body>
</html>
```